Harrow Tavern & Grille Menu Makeover

I am looking for a professional look to update our current menu. We are an independently owned sports bar and grill. Up to this point, I have done all of my own graphic designing. I am looking for something classy/family oriented. We are a very family friendly sports bar that offers a wide variety of menu options. Our website is www.harrowtavernco.example. This may help you get more of a feel for what type of place we are and what we offer. Our menu is listed on the website. My current menu is 8.5x14 inserts that feature a cover page, 4 inside pages and a back page. I would like something a little more condensed than this. Possibly a large tri-fold menu? I am open to all new ideas. I do have some pictures on my menu now, and would like to continue using a few pictures to feature some of my items. I would like something that is in a format that gives me the option to change items and prices on my own in the future. I would also like it to feature, or inform my patrons about our technology that we offer. We offer online ordering and we are a "verified venue" with Brewvoke.( a social site for craft beer lovers).

Industry/Entity Type

Sports Bar

Requirements
Nice to have
• Nice to have some pictures, but does not have to. We do feature 9 different beers on tap. A lot of them are local craft beers from the state of Kansas. Not sure if that is something we can feature, but it is a nice talking point. All of our tables and bar are hand built. With a rich mahogany finish on all of our woodwork, some type of "woodgrain" look into the menu would be nice.

```html
<!DOCTYPE html>
<html lang="en">
<head>
<meta charset="utf-8">
<title>Harrow Tavern &amp; Grille — Menu Cover</title>
<link rel="stylesheet" href="https://fonts.googleapis.com/css2?family=Cinzel:wght@700;800&display=swap">
<style>
  :root {
    --mahogany-dark: #5e1d0c;
    --mahogany: #8a3316;
    --mahogany-light: #a2451f;
    --parchment-light: #e9d3ac;
    --parchment: #d7b98a;
    --parchment-edge: #9c7446;
    --ink: #141008;
  }
  html, body {
    margin: 0;
    padding: 0;
    overflow: hidden;
  }
  .menu-cover {
    position: relative;
    width: 850px;
    height: 1200px;
    overflow: hidden;
    font-family: "Cinzel", "Times New Roman", serif;
  }
  .woodgrain {
    position: absolute;
    inset: 0;
    background:
      linear-gradient(90deg,
        var(--mahogany-dark) 0%, var(--mahogany) 12%, var(--mahogany-light) 30%,
        var(--mahogany) 48%, var(--mahogany-dark) 62%, var(--mahogany) 78%,
        var(--mahogany-light) 90%, var(--mahogany-dark) 100%);
  }
  .parchment {
    position: absolute;
    left: 44px;
    top: 194px;
    width: 760px;
    height: 494px;
    border-radius: 14px;
    background: radial-gradient(ellipse at 50% 50%,
      var(--parchment-light) 0%, var(--parchment) 60%, var(--parchment-edge) 100%);
    box-shadow: 0 6px 14px rgba(0, 0, 0, 0.45);
  }
  .title-rule {
    position: absolute;
    left: 0;
    width: 850px;
    height: 12px;
    overflow: visible;
  }
  .title-rule--top { top: 370px; }
  .title-rule--bottom { top: 520px; }
  .brand-name {
    position: absolute;
    left: 0;
    width: 850px;
    top: 388px;
    margin: 0;
    text-align: center;
    color: var(--ink);
    font-weight: 700;
    font-size: 46px;
    line-height: 70px;
    letter-spacing: 0.32em;
    text-indent: 0.32em;
  }
  .brand-name .initial {
    font-size: 66px;
  }
  .brand-tagline {
    position: absolute;
    left: 0;
    width: 850px;
    top: 472px;
    margin: 0;
    text-align: center;
    color: var(--ink);
    font-weight: 700;
    font-size: 27px;
    line-height: 36px;
    letter-spacing: 0.02em;
  }
  .brand-tagline .initial {
    font-size: 33px;
  }
</style>
</head>
<body>
  <main class="menu-cover">
    <div class="woodgrain" role="img" aria-label="Rich mahogany woodgrain planks"></div>
    <div class="parchment" role="img" aria-label="Aged, torn parchment sheet"></div>

    <svg class="title-rule title-rule--top" viewBox="0 0 850 12" aria-hidden="true">
      <line x1="140" y1="6" x2="712" y2="6" stroke="var(--ink)" stroke-width="2.4"/>
      <circle cx="134" cy="6" r="2.4" fill="var(--ink)"/>
      <circle cx="142" cy="6" r="3" fill="var(--ink)"/>
      <circle cx="718" cy="6" r="2.4" fill="var(--ink)"/>
      <circle cx="710" cy="6" r="3" fill="var(--ink)"/>
    </svg>

    <h1 class="brand-name"><span class="initial">H</span>ARROW</h1>
    <p class="brand-tagline"><span class="initial">T</span>AVERN &amp; <span class="initial">G</span>RILLE</p>

    <svg class="title-rule title-rule--bottom" viewBox="0 0 850 12" aria-hidden="true">
      <line x1="246" y1="6" x2="612" y2="6" stroke="var(--ink)" stroke-width="2.2"/>
      <circle cx="240" cy="6" r="2.2" fill="var(--ink)"/>
      <circle cx="248" cy="6" r="2.8" fill="var(--ink)"/>
      <circle cx="618" cy="6" r="2.2" fill="var(--ink)"/>
      <circle cx="610" cy="6" r="2.8" fill="var(--ink)"/>
    </svg>
  </main>
</body>
</html>
```